KV HOLDING Business Cards

I need business cards for "KV Holding group LLC" doublesided... logo on the back (also include logo on front)
logo attached to project... i have jpg up..
Company Info:
827 North Cadwell Avenue, Suite 4B
Chicago, Illinois 60654
facsimile 312-481-2075 (list fax, address, website on all cards.)
www.kvholdinggroup.example
Three different people on cards:
Darnell P. Okafor, CPA MST
Principal
ofc 312-481-3900
mobile 312-204-7751
darnellpokafor@kvholdinggroup.example
Hollis T. Brennecke, CPA MST
Principal
hollistbrennecke@kvholdinggroup.example
mobile 708-539-1184
ofc 312-481-3900
Conrad M Pavlik
Principal
ofc 312-481-3900
no mobile
conradmpavlik@kvholdinggroup.example
I have multiple projects listed.. see below:
Business cards for amber gate ventures llc
letterhead
envelopes
Business cards for KV Holding LLC
letterhead
envelopes
Target Market(s)
rich people
Industry/Entity Type
Business
Look and feel
Each slider illustrates characteristics of the customer's brand and the style your logo design should communicate.

```html
<!DOCTYPE html>
<html lang="en">
<head>
<meta charset="utf-8">
<title>KV Holding Group LLC — Business Cards</title>
<link rel="stylesheet" href="https://fonts.googleapis.com/css2?family=Roboto+Condensed:wght@300;400&display=swap">
<style>
  :root {
    --backdrop: #4a4a4a;
    --navy: #1d3f73;
    --card-grey: #c4c4c4;
    --card-white: #ffffff;
    --ink-light: #ffffff;
  }
  * { margin: 0; padding: 0; box-sizing: border-box; }
  html, body { width: 1200px; height: 1000px; overflow: hidden; }
  body { background: var(--backdrop); position: relative; font-family: "Roboto Condensed", Arial, sans-serif; }

  .card { position: absolute; width: 500px; height: 292px; overflow: hidden; }
  .card--back { left: 77px; background: var(--card-grey); }
  .card--front { left: 631px; background: var(--card-white); }
  .row-1 { top: 31px; }
  .row-2 { top: 348px; }
  .row-3 { top: 668px; }

  /* Back */
  .back__name {
    position: absolute; left: 0; right: 0; top: 184px;
    text-align: center; font-size: 34px; font-weight: 400;
    color: var(--navy); line-height: 1;
  }
  .back__web {
    position: absolute; left: 0; right: 0; top: 226px;
    text-align: center; font-size: 21px; font-weight: 400;
    color: var(--navy); letter-spacing: 2.5px; line-height: 1;
  }

  /* Front */
  .front__top-band { position: absolute; left: 0; top: 0; width: 100%; height: 10px; background: var(--navy); }
  .front__person { position: absolute; left: 36px; top: 76px; color: var(--navy); }
  .front__name { font-size: 23px; font-weight: 400; line-height: 1.1; }
  .front__title { font-size: 14px; font-weight: 400; line-height: 1.1; }
  .front__rule { position: absolute; left: 0; top: 121px; width: 284px; height: 3px; background: var(--navy); }
  .front__brand {
    position: absolute; left: 299px; top: 115px; width: 192px;
    font-size: 16px; font-weight: 400; color: var(--navy); white-space: nowrap; line-height: 1.1;
  }
  .front__contacts { position: absolute; left: 36px; top: 149px; list-style: none; color: var(--navy); font-size: 11.5px; font-weight: 400; line-height: 14.5px; }
  .row-2 .front__contacts { top: 152px; line-height: 17px; }
  .row-3 .front__contacts { top: 165px; line-height: 17px; }
  .front__bottom-band {
    position: absolute; left: 0; bottom: 0; width: 100%; height: 47px; background: var(--navy);
    color: var(--ink-light); font-size: 11px; font-weight: 400; padding-left: 36px; line-height: 47px; white-space: nowrap;
  }
</style>
</head>
<body>

  <section class="card card--back row-1">
    <p class="back__name">KV Holding Group LLC</p>
    <p class="back__web">www.kvholdinggroup.example</p>
  </section>
  <section class="card card--front row-1">
    <div class="front__top-band"></div>
    <div class="front__person">
      <h2 class="front__name">Darnell P. Okafor, CPA MST</h2>
      <p class="front__title">Principal</p>
    </div>
    <div class="front__rule"></div>
    <p class="front__brand">KV Holding Group LLC</p>
    <ul class="front__contacts">
      <li>Office : 312-481-3900</li>
      <li>Direct : 312-481-3618</li>
      <li>Mobile : 312-204-7751</li>
      <li>Facsimile : 312-481-2075</li>
      <li>Email : darnellpokafor@kvholdinggroup.example</li>
    </ul>
    <p class="front__bottom-band">827 North Cadwell Avenue, Suite 4B Chicago, Illinois 60654 &nbsp;|&nbsp; www.kvholdinggroup.example</p>
  </section>

  <section class="card card--back row-2">
    <p class="back__name">KV Holding Group LLC</p>
    <p class="back__web">www.kvholdinggroup.example</p>
  </section>
  <section class="card card--front row-2">
    <div class="front__top-band"></div>
    <div class="front__person">
      <h2 class="front__name">Hollis T. Brennecke, CPA MST</h2>
      <p class="front__title">Principal</p>
    </div>
    <div class="front__rule"></div>
    <p class="front__brand">KV Holding Group LLC</p>
    <ul class="front__contacts">
      <li>Office : 312-481-3900</li>
      <li>Mobile : 708-539-1184</li>
      <li>Facsimile : 312-481-2075</li>
      <li>Email : hollistbrennecke@kvholdinggroup.example</li>
    </ul>
    <p class="front__bottom-band">827 North Cadwell Avenue, Suite 4B Chicago, Illinois 60654 &nbsp;|&nbsp; www.kvholdinggroup.example</p>
  </section>

  <section class="card card--back row-3">
    <p class="back__name">KV Holding Group LLC</p>
    <p class="back__web">www.kvholdinggroup.example</p>
  </section>
  <section class="card card--front row-3">
    <div class="front__top-band"></div>
    <div class="front__person">
      <h2 class="front__name">Conrad M Pavlik</h2>
      <p class="front__title">Principal</p>
    </div>
    <div class="front__rule"></div>
    <p class="front__brand">KV Holding Group LLC</p>
    <ul class="front__contacts">
      <li>Office : 312-481-3900</li>
      <li>Facsimile : 312-481-2075</li>
      <li>Email : conradmpavlik@kvholdinggroup.example</li>
    </ul>
    <p class="front__bottom-band">827 North Cadwell Avenue, Suite 4B Chicago, Illinois 60654 &nbsp;|&nbsp; www.kvholdinggroup.example</p>
  </section>

</body>
</html>
```